Steadfast Corner Vending Needs a Promotional Flyer

Design a one page, one sided 8 1/2" x 11" flyer that can be handed out to potential customers. Please keep printing efficiencies in mind. See attached old flyers and company website (steadfastcornervend.example) for reference of services. I have also attached our current logo.

```html
<!DOCTYPE html>
<html lang="en">
<head>
<meta charset="utf-8">
<title>Steadfast Corner Vending – Flyer</title>
<link rel="stylesheet" href="https://fonts.googleapis.com/css2?family=Poppins:wght@400;500;600;700;800&display=swap">
<style>
  :root{
    --sky:#4cb0e4;
    --sky-deep:#2f95cf;
    --navy:#12263a;
    --panel:#0f2b45;
    --ink:#1d2b38;
    --red:#c8151b;
    --yellow:#ffe500;
    --paper:#ffffff;
    --backdrop:#e4e4e4;
  }
  *{margin:0;padding:0;box-sizing:border-box}
  html,body{width:1200px;height:2400px;overflow:hidden;background:var(--backdrop)}
  body{font-family:"Poppins",sans-serif;color:var(--ink);position:relative}
  .flyer{
    position:absolute;left:40px;top:475px;width:940px;height:1217px;
    transform:scale(1.1915);transform-origin:0 0;
    background:var(--paper);overflow:hidden;
    box-shadow:0 6px 24px rgba(0,0,0,.18);
  }
  .abs{position:absolute}
  .hero-shape{left:0;top:0}
  .machine-photo{
    left:66px;top:41px;width:340px;height:390px;
    background:linear-gradient(100deg,#2e9c7a 0%,#6fc7a8 22%,#3c3f44 30%,#1c2026 60%,#55595f 85%,#b9bdc2 100%);
    border-radius:4px;
  }
  .headline{left:492px;top:42px;color:var(--navy)}
  .headline .kicker{font-size:29px;font-weight:700;letter-spacing:4px;line-height:1}
  .headline .big{font-size:84px;font-weight:800;color:var(--sky);line-height:.78;letter-spacing:-1px;margin-top:8px;padding-top:6px}
  .headline .company{font-size:41px;font-weight:700;letter-spacing:9px;line-height:1;margin-top:6px}
  .tagline{left:492px;top:274px;padding-left:17px;border-left:2px solid var(--navy);font-size:18.5px;line-height:22px;font-weight:500;color:var(--navy);width:400px}
  .why-panel{left:490px;top:359px;width:450px;height:684px;background:linear-gradient(180deg,#123049,#0d2237);border-bottom-left-radius:26px}
  .why-head{left:490px;top:359px;width:450px;height:46px;background:var(--sky);border-top-left-radius:26px;color:#fff;font-size:29px;font-weight:700;letter-spacing:4.5px;padding-left:40px;line-height:48px}
  .reason{left:514px;width:400px;display:flex;gap:12px}
  .reason svg{flex:0 0 34px;margin-top:4px}
  .reason h3{font-size:16.5px;font-weight:700;color:var(--sky);line-height:19px}
  .reason p{font-size:13px;line-height:15px;color:#fff}
  .rule{left:514px;width:400px;border-top:1px dashed rgba(255,255,255,.35)}
  .services-title{left:51px;top:524px;font-size:31px;font-weight:700;color:var(--navy)}
  .services-title span{color:var(--sky)}
  .ribbon{left:54px;width:348px;height:34px}
  .ribbon .bar{position:absolute;inset:0;background:var(--sky);clip-path:polygon(0 0,100% 0,94% 100%,0 100%)}
  .ribbon .shade{position:absolute;left:0;right:14px;top:34px;height:4px;background:var(--navy);clip-path:polygon(0 0,100% 0,98% 100%,0 100%)}
  .ribbon span{position:relative;color:#fff;font-weight:600;font-size:19px;line-height:34px;padding-left:13px}
  .svc-copy{left:56px;width:360px;font-size:14px;line-height:16px;color:#2b3440}
  .brands{left:56px;top:811px;display:grid;grid-template-columns:118px 100px 84px 110px;font-size:12.5px;line-height:15px;white-space:nowrap}
  .brands i{font-style:normal;color:var(--sky);font-size:9px;margin-right:3px}
  .brands-note{left:56px;top:853px;font-size:12.5px;font-weight:700;white-space:nowrap}
  .brand-name{left:54px;top:1078px;display:flex;align-items:center;gap:10px}
  .brand-name .mark{width:20px;height:20px;background:var(--navy);flex:0 0 20px}
  .brand-name .word{font-size:23px;font-weight:700;color:var(--navy);line-height:27px;width:250px}
  .cta{left:344px;top:1063px;font-size:26px;font-weight:700;letter-spacing:2.4px;color:var(--navy);white-space:nowrap}
  .cta span{color:var(--sky)}
  .contact{left:346px;top:1104px;width:542px;display:flex;justify-content:space-between;font-size:18.5px;font-weight:500;color:var(--navy);white-space:nowrap}
  .contact div{display:flex;align-items:center;gap:6px}
  .url-bar{left:344px;top:1140px;width:542px;height:30px;background:var(--sky);border-radius:3px;display:flex;align-items:center;padding:0 14px;justify-content:space-between}
  .url-bar small{font-size:8px;letter-spacing:2px;color:var(--navy);font-weight:500}
  .url-bar b{font-size:16px;letter-spacing:1.3px;color:var(--navy);white-space:nowrap}
  .url-bar b em{font-style:normal;color:#fff}
</style>
</head>
<body>
<main class="flyer">
  <svg class="abs hero-shape" width="940" height="520" viewBox="0 0 940 520">
    <path d="M0 0 H430 C500 110 500 300 400 400 C320 475 140 490 0 445 Z" fill="var(--sky)"/>
  </svg>
  <div class="abs machine-photo" role="img" aria-label="Photo of a combined snack, drinks and coffee vending machine"></div>

  <svg class="abs" style="left:274px;top:361px" width="200" height="200" viewBox="-100 -100 200 200" aria-label="More than 30 years of experience badge">
    <polygon fill="var(--red)" points="0,-96 16,-82 36,-89 44,-70 66,-69 65,-48 84,-38 74,-18 88,0 74,18 84,38 65,48 66,69 44,70 36,89 16,82 0,96 -16,82 -36,89 -44,70 -66,69 -65,48 -84,38 -74,18 -88,0 -74,-18 -84,-38 -65,-48 -66,-69 -44,-70 -36,-89 -16,-82"/>
    <text x="0" y="-40" text-anchor="middle" font-family="Poppins,sans-serif" font-size="12.5" font-weight="500" letter-spacing="2" fill="#fff">MORE THAN</text>
    <text x="0" y="14" text-anchor="middle" font-family="Poppins,sans-serif" font-size="52" font-weight="800" fill="var(--yellow)">30+</text>
    <text x="0" y="34" text-anchor="middle" font-family="Poppins,sans-serif" font-size="12.5" font-weight="500" letter-spacing="2" fill="#fff">YEARS OF</text>
    <text x="0" y="52" text-anchor="middle" font-family="Poppins,sans-serif" font-size="12.5" font-weight="500" letter-spacing="2" fill="#fff">EXPERIENCE</text>
  </svg>

  <header class="abs headline">
    <div class="kicker">CHICAGOLAND'S</div>
    <div class="big">PREMIER<br>VENDING</div>
    <div class="company">COMPANY</div>
  </header>
  <p class="abs tagline">Our vending machine services are designed to cater to your every craving and refreshment need..</p>

  <section>
    <div class="abs why-panel"></div>
    <h2 class="abs why-head">WHY CHOOSE US?</h2>

    <div class="abs reason" style="top:433px">
      <svg width="34" height="34" viewBox="0 0 34 34" fill="none" stroke="#9fb3c6" stroke-width="1.6"><circle cx="17" cy="14" r="10"/><path d="M17 8v12M14 11h5M14 17h5M6 28h22"/></svg>
      <div><h3>Zero Cost to you</h3><p>We provide state-of-the-art vending machines at NO COST TO YOU.</p></div>
    </div>
    <div class="abs rule" style="top:487px"></div>
    <div class="abs reason" style="top:495px">
      <svg width="34" height="34" viewBox="0 0 34 34" fill="none" stroke="#9fb3c6" stroke-width="1.6"><rect x="4" y="10" width="8" height="16"/><path d="M12 12l8-6 10 6v12H12"/></svg>
      <div><h3>Reliability</h3><p>We are local owner/ operators that truly care about our most valuable asset - YOU, the customer.</p></div>
    </div>
    <div class="abs rule" style="top:550px"></div>
    <div class="abs reason" style="top:558px">
      <svg width="34" height="34" viewBox="0 0 34 34" fill="none" stroke="#9fb3c6" stroke-width="1.6"><path d="M6 28V14l8-6 8 6v14zM22 20h8v8h-8"/><circle cx="26" cy="8" r="4"/></svg>
      <div><h3>Convenience</h3><p>Say goodbye to time-consuming trips to the store. With our vending machines, your favorite snacks, drinks, and essentials are just a few steps away, available 24/7.</p></div>
    </div>
    <div class="abs rule" style="top:642px"></div>
    <div class="abs reason" style="top:650px">
      <svg width="34" height="34" viewBox="0 0 34 34" fill="none" stroke="#9fb3c6" stroke-width="1.6"><circle cx="17" cy="20" r="10"/><path d="M12 21l4 4 7-8M6 6l2 2M17 3v3M28 6l-2 2"/></svg>
      <div><h3>Quality</h3><p>We stock our vending machines with high-quality, fresh products from trusted brands.</p></div>
    </div>
    <div class="abs rule" style="top:705px"></div>
    <div class="abs reason" style="top:713px">
      <svg width="34" height="34" viewBox="0 0 34 34" fill="none" stroke="#9fb3c6" stroke-width="1.6"><circle cx="17" cy="17" r="12"/><circle cx="17" cy="17" r="5"/><path d="M17 5v7M17 22v7M5 17h7M22 17h7"/></svg>
      <div><h3>Variety</h3><p>We understand that different people have different tastes. That's why we offer a wide range of snacks, beverages, and everyday essentials, including healthy options, to satisfy every palate.</p></div>
    </div>
    <div class="abs rule" style="top:797px"></div>
    <div class="abs reason" style="top:805px">
      <svg width="34" height="34" viewBox="0 0 34 34" fill="none" stroke="#9fb3c6" stroke-width="1.6"><circle cx="17" cy="17" r="12"/><path d="M11 23l10-10 3 3-10 10h-3z"/></svg>
      <div><h3>Customization</h3><p>We can customize our vending services to suit your preferences.</p></div>
    </div>
    <div class="abs rule" style="top:860px"></div>
    <div class="abs reason" style="top:868px">
      <svg width="34" height="34" viewBox="0 0 34 34" fill="none" stroke="#9fb3c6" stroke-width="1.6"><rect x="11" y="11" width="12" height="12"/><path d="M14 5v6M20 5v6M14 23v6M20 23v6M5 14h6M5 20h6M23 14h6M23 20h6"/></svg>
      <div><h3>Technology</h3><p>Our vending machines are equipped with state-of-the-art technology, making payments easy with a variety of options, including contactless payments and mobile apps.</p></div>
    </div>
    <div class="abs rule" style="top:952px"></div>
    <div class="abs reason" style="top:960px">
      <svg width="34" height="34" viewBox="0 0 34 34" fill="none" stroke="#9fb3c6" stroke-width="1.6"><circle cx="17" cy="17" r="12"/><circle cx="17" cy="17" r="5"/><path d="M17 9v3M17 22v3M9 17h3M22 17h3"/></svg>
      <div><h3>On-time Maintenance</h3><p>Our proactive maintenance team ensures that you always have a hassle-free experience.</p></div>
    </div>
  </section>

  <section>
    <h2 class="abs services-title">Our <span>Services</span></h2>

    <div class="abs ribbon" style="top:591px"><div class="shade"></div><div class="bar"></div><span>Vending Machine Services</span></div>
    <p class="abs svc-copy" style="top:640px">At Steadfast Corner Vending, we're here to revolutionize the way you experience snacks and beverages.</p>

    <div class="abs ribbon" style="top:705px"><div class="shade"></div><div class="bar"></div><span>Coffee Services</span></div>
    <p class="abs svc-copy" style="top:753px;width:375px">At Steadfast Corner Vending, we are committed to delivering exceptional coffee and other hot beverage experiences to our customers.</p>
    <div class="abs brands">
      <div><i>●</i>Brightcup</div><div><i>●</i>Birchpeak</div><div><i>●</i>Oakmill</div><div><i>●</i>Kettle House</div>
      <div><i>●</i>Morning Ring</div><div><i>●</i>Northvale</div><div><i>●</i>Goldcrest</div><div></div>
    </div>
    <p class="abs brands-note">and other specialty brands upon request</p>

    <div class="abs ribbon" style="top:880px"><div class="shade"></div><div class="bar"></div><span>Pantry Services</span></div>
    <p class="abs svc-copy" style="top:928px;width:395px">Elevate the break room experience in your office with a customized selection of snacks, beverages, and kitchen essentials, all conveniently accessible in your workplace pantry.</p>
  </section>

  <footer>
    <div class="abs brand-name"><div class="mark"></div><div class="word">STEADFAST CORNER<br>VENDING</div></div>
    <div class="abs cta">GIVE US A CALL <span>OR DROP US A LINE!</span></div>
    <div class="abs contact">
      <div><svg width="18" height="18" viewBox="0 0 18 18"><circle cx="9" cy="9" r="8.5" fill="var(--sky)"/><path d="M6 4.5l2 2-1 1.3c.6 1.3 1.6 2.3 2.9 2.9l1.3-1 2 2-1.4 1.5C8.6 13 5 9.4 4.6 5.9z" fill="#fff"/></svg>555-014-7720</div>
      <div><svg width="18" height="18" viewBox="0 0 18 18"><circle cx="9" cy="9" r="8.5" fill="var(--sky)"/><rect x="4.5" y="6" width="9" height="6.5" fill="none" stroke="#fff" stroke-width="1.2"/><path d="M4.5 6l4.5 3.5L13.5 6" fill="none" stroke="#fff" stroke-width="1.2"/></svg>info@steadfastcornervend.example</div>
    </div>
    <div class="abs url-bar"><small>OR VISIT US AT</small><b>www.<em>steadfastcornervend</em>.example</b></div>
  </footer>
</main>
</body>
</html>
```